Lawn sign for construction company

Would like this to be a very clean and high end design for luxury homes. We need a yard sign designed that includes the company logo, website, phone number and major service offerings (residential and commercial renovations and maintenance)
The company website is brackwellbuilders.com all other contact info is in the attachments
Target Market(s)
Luxury home owners and business owners
Industry/Entity Type
Construction/Home Improvement
Font styles to use
Other font styles liked:
- See company logo and other graphics included for title text fonts. All other fonts can be standard sans serif.
Colors
0054AA
0677BA
7BADD7
CADEEF
E8F1F8
Requirements
Must have
- Clean, easy to read design, would like 2 sided sign. A main sign side and back side which states “free estimates, and includes the website and phone number. Must also match the color scheme of the provided logo and other company images. Dark Navy blue primary color, gray secondary color, and orange as an accent color.
Nice to have
- 2nd sign side very simple design
Should not have
- Too many graphics limit to 1-3 colors

```html
<!DOCTYPE html>
<html lang="en">
<head>
<meta charset="utf-8">
<title>Brackwell Builders – Yard Sign, Front and Back</title>
<link rel="stylesheet" href="https://fonts.googleapis.com/css2?family=Montserrat:wght@600;700;800&display=swap">
<style>
  :root {
    --stage: #777677;
    --frame: #d6d6d6;
    --panel: #cbcbcb;
    --panel-light: #dcdcdc;
    --navy: #020759;
    --orange: #e8760b;
    --white: #ffffff;
  }
  * { box-sizing: border-box; margin: 0; padding: 0; }
  html, body {
    width: 1200px; height: 1200px; overflow: hidden;
    background: var(--stage);
    font-family: "Montserrat", Arial, sans-serif;
  }
  .sign {
    position: absolute; left: 225px;
    width: 750px; height: 506px;
    background: var(--frame);
    padding: 17px;
  }
  .sign--front { top: 50px; }
  .sign--back { top: 636px; }
  .sign__face {
    position: relative; width: 716px; height: 472px;
    border: 1.5px solid var(--navy);
    overflow: hidden;
  }
  .sign__bg { position: absolute; inset: 0; width: 100%; height: 100%; }
  .brand {
    position: absolute; left: 0; right: 0; top: 118px;
    display: flex; justify-content: center; align-items: center; gap: 14px;
  }
  .brand__mark { width: 22px; height: 22px; background: var(--orange); }
  .brand__name {
    color: var(--orange); font-weight: 800; font-size: 44px;
    letter-spacing: 1px; text-transform: uppercase;
  }
  .line { position: absolute; left: 0; right: 0; text-align: center; white-space: nowrap; }
  .tagline {
    top: 326px; color: var(--white); font-weight: 700; font-size: 31px; letter-spacing: 2.5px;
  }
  .phone-big {
    top: 360px; display: flex; justify-content: center; align-items: center; gap: 10px;
    color: var(--white); font-weight: 700; font-size: 74px; letter-spacing: 1px; line-height: 1;
  }
  .phone-big svg { width: 46px; height: 50px; margin-top: 4px; }
  .web-front {
    top: 432px; color: var(--orange); font-weight: 700; font-size: 26px; letter-spacing: 3.5px;
  }
  .services {
    top: 340px; color: var(--white); font-weight: 700; font-size: 25px;
    line-height: 30px; letter-spacing: 1px;
  }
  .services .dot {
    display: inline-block; width: 13px; height: 13px; background: var(--orange);
    margin: 0 8px 2px 4px; vertical-align: middle;
  }
  .rule {
    position: absolute; left: 29px; right: 29px; top: 415px; height: 2px; background: var(--orange);
  }
  .contact-row {
    top: 424px; display: flex; justify-content: center; align-items: center; gap: 10px;
    color: var(--orange); font-weight: 700; font-size: 28px;
  }
  .contact-row svg { width: 22px; height: 22px; }
  .contact-row .sep { color: var(--orange); margin: 0 4px; }
</style>
</head>
<body>

<section class="sign sign--front">
  <div class="sign__face">
    <svg class="sign__bg" viewBox="0 0 716 472" preserveAspectRatio="none" aria-hidden="true">
      <rect width="716" height="472" fill="var(--panel)"/>
      <polygon points="700,0 716,0 716,472 260,330" fill="var(--panel-light)"/>
      <polygon points="0,219 358,321 716,219 716,472 0,472" fill="var(--orange)"/>
      <polygon points="25,227 358,322 690,227 716,224 716,472 0,472 0,220" fill="var(--navy)"/>
      <polygon points="0,219 25,227 358,320 358,330 0,227" fill="var(--navy)"/>
      <polygon points="716,219 690,227 358,320 358,330 716,227" fill="var(--navy)"/>
      <polygon points="25,227 358,320 690,227 358,312" fill="var(--orange)"/>
    </svg>
    <div class="brand">
      <span class="brand__mark"></span>
      <span class="brand__name">Brackwell Builders</span>
    </div>
    <p class="line tagline">CALL FOR FREE ESTIMATES</p>
    <p class="line phone-big">
      <svg viewBox="0 0 46 50" aria-hidden="true">
        <path d="M6 14c-2 10 8 26 20 31 4 2 8 0 9-3l1-3c0-2-1-3-2-4l-6-3c-1 0-3 0-4 1l-2 3c-5-3-9-8-11-13l3-2c1-1 1-2 1-3l-2-7c-1-1-2-2-4-2l-3 1z" fill="var(--orange)"/>
        <path d="M24 14a8 8 0 0 1 8 8M24 7a15 15 0 0 1 15 15M24 0a22 22 0 0 1 22 22" fill="none" stroke="var(--orange)" stroke-width="3"/>
      </svg>
      800-555-0143
    </p>
    <p class="line web-front">www.brackwellbuilders.com</p>
  </div>
</section>

<section class="sign sign--back">
  <div class="sign__face">
    <svg class="sign__bg" viewBox="0 0 716 472" preserveAspectRatio="none" aria-hidden="true">
      <rect width="716" height="472" fill="var(--panel)"/>
      <polygon points="700,0 716,0 716,472 260,330" fill="var(--panel-light)"/>
      <polygon points="0,219 358,321 716,219 716,472 0,472" fill="var(--navy)"/>
      <polygon points="25,227 358,320 690,227 358,312" fill="var(--orange)"/>
    </svg>
    <div class="brand">
      <span class="brand__mark"></span>
      <span class="brand__name">Brackwell Builders</span>
    </div>
    <p class="line services">RESIDENTIAL RENOVATIONS<span class="dot"></span> COMMERCIAL<br>RENOVATIONS<span class="dot"></span> MAINTENANCE</p>
    <div class="rule"></div>
    <p class="line contact-row">
      <svg viewBox="0 0 46 50" aria-hidden="true">
        <path d="M6 14c-2 10 8 26 20 31 4 2 8 0 9-3l1-3c0-2-1-3-2-4l-6-3c-1 0-3 0-4 1l-2 3c-5-3-9-8-11-13l3-2c1-1 1-2 1-3l-2-7c-1-1-2-2-4-2l-3 1z" fill="var(--white)"/>
        <path d="M24 14a8 8 0 0 1 8 8M24 7a15 15 0 0 1 15 15" fill="none" stroke="var(--white)" stroke-width="3"/>
      </svg>
      <span>800.555.0143</span>
      <span class="sep">|</span>
      <svg viewBox="0 0 24 24" aria-hidden="true">
        <circle cx="12" cy="12" r="10" fill="none" stroke="var(--white)" stroke-width="1.6"/>
        <ellipse cx="12" cy="12" rx="4.5" ry="10" fill="none" stroke="var(--white)" stroke-width="1.4"/>
        <path d="M2 12h20M4 7h16M4 17h16" stroke="var(--white)" stroke-width="1.3"/>
      </svg>
      <span>www.brackwellbuilders.com</span>
    </p>
  </div>
</section>

</body>
</html>
```